Corvane Capital Business Cards

These are professional business cards that are for my family office.
Put fake emails and phone numbers as of now until I finalize those components. This family office controls my families investments, assets, and future. The cards should be professional.
..
.
.
.
I just uploaded another variation of a logo I would like to see as a business card to I am inbeteen which logo to use

Target Market(s)

business

Industry/Entity Type

business

Contact Information for Business Card

Professional, wealth related, finance related.

Requirements
Must have
• Logo

```html
<!DOCTYPE html>
<html lang="en">
<head>
<meta charset="utf-8">
<title>Corvane Capital Business Cards</title>
<link rel="stylesheet" href="https://fonts.googleapis.com/css2?family=Playfair+Display:wght@400&family=Tinos:wght@400;700&display=swap">
<style>
  :root {
    --backdrop: #e8e3dc;
    --card-white: #ffffff;
    --ink: #000000;
    --gold: #c5ad6e;
    --shadow: rgba(40, 28, 15, 0.35);
  }
  * { margin: 0; padding: 0; box-sizing: border-box; }
  html, body {
    width: 1200px;
    height: 749px;
    overflow: hidden;
    background: var(--backdrop);
  }
  .canvas {
    position: relative;
    width: 1200px;
    height: 749px;
  }
  .card {
    position: absolute;
    top: 226px;
    width: 502px;
    height: 286px;
    box-shadow: 0 3px 8px var(--shadow);
    overflow: hidden;
  }
  .card--front { left: 98px; background: var(--card-white); }
  .card--back { left: 608px; background: var(--gold); }

  .brand-mark {
    position: absolute;
  }
  .card--front .brand-mark {
    left: 300px;
    top: 58px;
    width: 170px;
    height: 170px;
    background: var(--ink);
  }
  .card--back .brand-mark {
    left: 70px;
    top: 40px;
    width: 150px;
    height: 150px;
    background: var(--card-white);
  }

  .wordmark {
    font-family: "Playfair Display", serif;
    font-weight: 400;
    letter-spacing: 0.02em;
    white-space: nowrap;
  }
  .card--front .wordmark {
    position: absolute;
    left: 18px;
    top: 33px;
    font-size: 21px;
    color: var(--ink);
  }
  .wordmark__accent { color: var(--gold); }
  .card--back .wordmark {
    position: absolute;
    right: 17px;
    bottom: 24px;
    font-size: 25px;
    color: var(--card-white);
  }

  .holder {
    position: absolute;
    left: 18px;
    top: 152px;
    font-family: "Tinos", serif;
  }
  .holder__name {
    font-size: 18px;
    font-weight: 700;
    color: var(--ink);
    line-height: 1.2;
  }
  .holder__surname { color: var(--gold); }
  .holder__role {
    font-size: 14px;
    color: var(--ink);
    margin-top: 1px;
  }
  .holder__rule {
    width: 17px;
    height: 4px;
    background: var(--gold);
    margin-top: 10px;
  }
  .contact {
    position: absolute;
    left: 18px;
    top: 228px;
    list-style: none;
    font-family: "Tinos", serif;
    font-size: 14px;
    color: var(--ink);
  }
  .contact__item {
    display: flex;
    align-items: center;
    gap: 6px;
    height: 21px;
  }
  .contact__icon { width: 13px; height: 11px; fill: var(--gold); }
</style>
</head>
<body>
<main class="canvas">
  <section class="card card--front" aria-label="Business card front">
    <div class="brand-mark" role="img" aria-label="Company logo symbol"></div>
    <p class="wordmark">CORVANE <span class="wordmark__accent">CAPITAL</span></p>
    <div class="holder">
      <p class="holder__name">Elias <span class="holder__surname">Hartley</span></p>
      <p class="holder__role">Founder</p>
      <div class="holder__rule"></div>
    </div>
    <ul class="contact">
      <li class="contact__item">
        <svg class="contact__icon" viewBox="0 0 13 11" aria-hidden="true">
          <path d="M1 3.5C1 2 3 1 6.5 1S12 2 12 3.5v1H9.5V3.2c-1.8-.5-4.2-.5-6 0v1.3H1z"/>
          <path d="M3 5h7l2 4.5v.5H1v-.5zM6.5 6a1.4 1.4 0 1 0 0 2.8 1.4 1.4 0 0 0 0-2.8z"/>
        </svg>
        <span>123-456-7890</span>
      </li>
      <li class="contact__item">
        <svg class="contact__icon" viewBox="0 0 13 11" aria-hidden="true">
          <path d="M0.5 1.5h12v1L6.5 6.3 0.5 2.5z"/>
          <path d="M0.5 3.8l6 3.8 6-3.8v5.7h-12z"/>
        </svg>
        <span>info@yourmailhere.com</span>
      </li>
    </ul>
  </section>

  <section class="card card--back" aria-label="Business card back">
    <div class="brand-mark" role="img" aria-label="Company logo symbol"></div>
    <p class="wordmark">CORVANE CAPITAL</p>
  </section>
</main>
</body>
</html>
```